Meridian Tidewren Pale Ale Beer Label/Badge

We need a Beer Label designed for our first official beer to be launched under The meridian Brand!!
It will be a Pale Ale Called "Tidewren Pale Ale"!

The Meridian has the largest Craft Beer & Cider selection in the Geelong & Surf Coast region. With a funky location and a relaxed vibe, Meridian prides itself on serving delicious, unique seasonal food paired with Australia's best Craft Beer. The meridian is the perfect setting for a relaxed afternoon or evening with friends and can package an experience for larger groups or corporate bookings.

The Meridian Tavern brand has been growing for over a year and a half and the first label needs to integrate The meridian Logo but at the same time bring a fresh, new and eye catching feel to it along with embracing the "Odysseus" story in which we will be naming future beers.

The story of Tidewren is found via the following link
http://lorevault.example/wiki/Tidewren_(folklore)

We expect designers to research The meridian Tavern brand along with the all important Craft Beer Market and demographics. This will, potentially, be the start of many more labels to come for the winning designer!!

Requirements
Must have
• The original "O" needs to be integrated into the new logo and as much as the Greek mythology is being used it needs to be certain that this is an original Australian Craft Beer in the modern age!!
strong, modern & unique!!
Nice to have
• Logo could have a depiction of Tidewren
Should not have
• tackiness or cheap!!

```html
<!DOCTYPE html>
<html lang="en">
<head>
<meta charset="utf-8">
<title>Meridian Tidewren Pale Ale Label</title>
<link rel="stylesheet" href="https://fonts.googleapis.com/css2?family=Rye&family=Lobster&family=Josefin+Sans:wght@600&display=swap">
<style>
  :root {
    --paper: #ffffff;
    --ink-grey: #4a4a4c;
    --ale-red: #8b2621;
    --wheat: #d6cda0;
  }
  html, body {
    margin: 0;
    padding: 0;
    overflow: hidden;
    background: var(--paper);
  }
  .label {
    position: relative;
    width: 1200px;
    height: 1000px;
    background: var(--paper);
    overflow: hidden;
  }
  .centered {
    position: absolute;
    left: 0;
    width: 1200px;
    text-align: center;
    margin: 0;
    line-height: 1;
  }
  .brand-mark {
    position: absolute;
    left: 581px;
    top: 130px;
    width: 28px;
    height: 28px;
    border-radius: 50%;
    background: var(--ink-grey);
  }
  .brand-name {
    top: 186px;
    font-family: "Josefin Sans", sans-serif;
    font-weight: 600;
    font-size: 66px;
    letter-spacing: 3px;
    color: var(--ink-grey);
  }
  .brand-tagline {
    top: 257px;
    font-family: "Josefin Sans", sans-serif;
    font-weight: 600;
    font-size: 23px;
    letter-spacing: 4px;
    color: var(--ink-grey);
  }
  .ornament-area {
    position: absolute;
    left: 350px;
    top: 280px;
    width: 490px;
    height: 250px;
  }
  .kicker {
    top: 552px;
    font-family: "Rye", serif;
    font-size: 28px;
    letter-spacing: 1px;
    color: var(--ink-grey);
  }
  .beer-name {
    top: 578px;
    font-family: "Rye", serif;
    font-size: 100px;
    letter-spacing: 1px;
    color: var(--ale-red);
    text-shadow: 4px 6px 0 var(--wheat);
  }
  .style-name {
    top: 694px;
    font-family: "Lobster", cursive;
    font-size: 82px;
    color: var(--ink-grey);
    text-shadow: 3px 5px 0 var(--wheat);
  }
  .divider {
    position: absolute;
    left: 380px;
    width: 440px;
    height: 26px;
  }
  .divider--upper { top: 678px; }
  .divider--lower { top: 784px; }
  .abv {
    top: 822px;
    font-family: "Rye", serif;
    font-size: 20px;
    color: var(--ink-grey);
  }
  .origin {
    top: 852px;
    font-family: "Lobster", cursive;
    font-size: 28px;
    color: var(--ale-red);
  }
</style>
</head>
<body>
<main class="label">
  <span class="brand-mark" aria-hidden="true"></span>
  <p class="centered brand-name">MERIDIAN</p>
  <p class="centered brand-tagline">TAVERN + BREWERY</p>

  <svg class="ornament-area" role="img" aria-label="Decorative ornament area in red and wheat tones" viewBox="0 0 490 250">
    <defs>
      <radialGradient id="ornamentFill" cx="50%" cy="50%" r="50%">
        <stop offset="0%" stop-color="#8b2621"/>
        <stop offset="40%" stop-color="#8b2621"/>
        <stop offset="65%" stop-color="#d6cda0"/>
        <stop offset="100%" stop-color="#ffffff" stop-opacity="0"/>
      </radialGradient>
    </defs>
    <rect x="0" y="0" width="490" height="250" rx="40" fill="url(#ornamentFill)"/>
  </svg>

  <p class="centered kicker">HANDCRAFTED BEER</p>
  <h1 class="centered beer-name">TIDEWREN</h1>

  <svg class="divider divider--upper" viewBox="0 0 440 26" aria-hidden="true">
    <line x1="30" y1="13" x2="410" y2="13" stroke="var(--wheat)" stroke-width="3"/>
    <polygon points="0,13 22,5 38,13 22,21" fill="none" stroke="var(--wheat)" stroke-width="3"/>
    <polygon points="440,13 418,5 402,13 418,21" fill="none" stroke="var(--wheat)" stroke-width="3"/>
  </svg>

  <h2 class="centered style-name">Pale Ale</h2>

  <svg class="divider divider--lower" viewBox="0 0 440 26" aria-hidden="true">
    <line x1="30" y1="14" x2="146" y2="14" stroke="var(--wheat)" stroke-width="3"/>
    <line x1="294" y1="14" x2="410" y2="14" stroke="var(--wheat)" stroke-width="3"/>
    <polygon points="0,14 22,6 38,14 22,22" fill="none" stroke="var(--wheat)" stroke-width="3"/>
    <polygon points="440,14 418,6 402,14 418,22" fill="none" stroke="var(--wheat)" stroke-width="3"/>
    <polygon points="160,3 163,10 171,10 165,15 167,23 160,18 153,23 155,15 149,10 157,10" fill="var(--ale-red)"/>
    <polygon points="220,0 224,9 234,9 226,15 229,25 220,19 211,25 214,15 206,9 216,9" fill="var(--ale-red)"/>
    <polygon points="280,3 283,10 291,10 285,15 287,23 280,18 273,23 275,15 269,10 277,10" fill="var(--ale-red)"/>
  </svg>

  <p class="centered abv">ABV 5%</p>
  <p class="centered origin">Kestrel Downs, Victoria, Australia</p>
</main>
</body>
</html>
```